wardrobe/costume stylist needs good business card for own business

Hi:)

I'm wanting a business card for my company. I am a freelance stylist.

I do wardrobe/costume stylist to TV commercials; Films; Fashion and Lifestyle shoots.

I'd like a design based around my name Rosalind Parfrey written nicely, maybe a colour? Up to you?!

I've attached a couple of images of business cards I like
.... be creative and have fun!

Thank you :)

Reason: I was trying to get my new business card ready for before I headed overseas Friday morning but I don't think that was realistic so I'd like to extend the deadline to give time to the project. Thank you

Hi designers:) Thank you for all your designs, I've extended the deadline until Sunday, so there's a bit more time. I've attached 3 pictures of business cards which I quite like, please take a look to see if it can be of help in your process. I like the pale plain or patterned background with dark font and the dark plain or patterned background with the pale font the motifs the feminine fonts the plain fonts I like the idea of playing with a circle or some shape on one side of the card with my name or initials as in the picture I have on my post could you play around with this idea a bit please? Thank you all for the work you've done :) Rosa

Hi I am working overseas til Saturday night sorry for no feedback until I teturn Thanks :) Rosa

Hi designers, Thank you all so much for submitting your designs, I really appreciate your input into my project :) I'm sorry I didn't get to respond to some comments, and give feedback. I didn't back from being away until later than I expected, and the deadline had passed then, so apologies. Thanks to you all again for all your really good designs :) Rosa

Target Market(s)

I am a freelance stylist my target audience is producers, production companies, photographers, directors...

Industry/Entity Type

Business

Requirements
Must have
• Rosalind Parfrey
Stylist or Wardrobe Stylist

email rosaparfrey@mailbox-example.co.nz
Mobile 0218467193

(Don't have to use the words 'email' and 'mobile')
Nice to have
• Would like it to be double sided
Like B & W
Like pale colour background with dark font or white font
Like dark colour background with pale font
Should not have
• I would prefer it not to incorporate pictures

```html
<!DOCTYPE html>
<html lang="en">
<head>
<meta charset="utf-8">
<title>Rosalind Parfrey – Wardrobe Stylist</title>
<link rel="stylesheet" href="https://fonts.googleapis.com/css2?family=UnifrakturCook:wght@700&family=Oswald:wght@600&family=Questrial&display=swap">
<style>
  :root {
    --card-brown: #4b2514;
    --card-brown-deep: #3d1c0e;
    --card-brown-light: #5a2f1b;
    --ornament-cream: #d9c7b8;
    --text-pale: #fbf6f1;
  }
  html, body {
    margin: 0;
    padding: 0;
    width: 1200px;
    height: 702px;
    overflow: hidden;
    background: var(--card-brown);
  }
  .business-card {
    position: relative;
    width: 1200px;
    height: 702px;
    overflow: hidden;
    background:
      radial-gradient(ellipse at 70% 40%, var(--card-brown-light) 0%, var(--card-brown) 55%, var(--card-brown-deep) 100%);
    color: var(--text-pale);
  }
  .floral-ornament {
    position: absolute;
    left: 0;
    top: 0;
    width: 500px;
    height: 702px;
  }
  .identity {
    position: absolute;
    left: 567px;
    top: 196px;
  }
  .stylist-name {
    margin: 0;
    font-family: "UnifrakturCook", serif;
    font-weight: 700;
    font-size: 60px;
    line-height: 1;
    letter-spacing: 1px;
  }
  .stylist-role {
    margin: 10px 0 0 8px;
    font-family: "Questrial", sans-serif;
    font-size: 32px;
    line-height: 1;
    letter-spacing: 2px;
    transform: scaleX(0.86);
    transform-origin: left center;
  }
  .contact-list {
    position: absolute;
    left: 567px;
    top: 362px;
    margin: 0;
    padding: 0;
    list-style: none;
  }
  .contact-item {
    display: flex;
    align-items: center;
    height: 78px;
  }
  .contact-label {
    width: 101px;
    font-family: "Oswald", sans-serif;
    font-weight: 600;
    font-size: 64px;
    line-height: 1;
  }
  .contact-value {
    font-family: "Questrial", sans-serif;
    font-size: 46px;
    line-height: 1;
    letter-spacing: 1px;
  }
  .contact-value--email {
    font-size: 36px;
    letter-spacing: 0.5px;
  }
</style>
</head>
<body>
  <main class="business-card">
    <svg class="floral-ornament" role="img" aria-label="White flowing floral swirl ornament with leaves and small butterflies" viewBox="0 0 500 702" preserveAspectRatio="none">
      <defs>
        <linearGradient id="ornament-fill" x1="0" y1="0" x2="1" y2="0">
          <stop offset="0" stop-color="var(--ornament-cream)" stop-opacity="0.35"/>
          <stop offset="1" stop-color="var(--ornament-cream)" stop-opacity="0"/>
        </linearGradient>
      </defs>
      <rect width="500" height="702" fill="url(#ornament-fill)"/>
    </svg>

    <header class="identity">
      <h1 class="stylist-name">Rosalind Parfrey</h1>
      <p class="stylist-role">WARDROBE STYLIST</p>
    </header>

    <ul class="contact-list">
      <li class="contact-item">
        <span class="contact-label">M</span>
        <span class="contact-value">0218467193</span>
      </li>
      <li class="contact-item">
        <span class="contact-label">E</span>
        <span class="contact-value contact-value--email">rosaparfrey@mailbox-example.co.nz</span>
      </li>
    </ul>
  </main>
</body>
</html>
```